BrivoTerna. Lantern of the Steady Harvest. Business card

Professional business card for BrivoTerna (Lantern of the Steady Harvest)
My rationale: Strategy-> Execution-> Results-> Value that lead to the BrivoTerna name: We put the Lantern of the Steady Harvest.
We deliver value to our customers helping them at defining a good strategy (cyan arrow). 90% of well formulated strategies fail due to poor execution so we also consider strategical execution very important (green arrow). Due to the execution we obtain the results (blue arrow). Finally, the results provide feedback to redefine strategy, and the new strategy has to be executed and new results obtained providing new feedback and on and on. It's like a wheel that finally, must create corporate value: value for shareholders, staholders, employees, providers...-

Target Market(s)

CEOs and steering comitees , invewrnent funds

Industry/Entity Type

Business Consultant

Contact Information for Business Card

Teodoro Vinsquel
CEO & Founder
teodoro.vinsquel@brivoterna-example.com
Mobile: +34 655.803.912
www.brivoterna-example.com

Colors

Designer to choose colors to be used in the design.

Requirements
Nice to have
• Nice to hace the words: Strategy, execution, results
• Nice to vave the claim: Lantern of the Steady Harvest
• The three colors should be shown:
• cyan for STRATEGY
• green for EXECUTION
• blue for RESULTS
Should not have
• Complete black background

```html
<!DOCTYPE html>
<html lang="en">
<head>
<meta charset="utf-8">
<title>BrivoTerna – Business Card</title>
<link rel="stylesheet" href="https://fonts.googleapis.com/css2?family=Josefin+Sans:wght@300;400;600;700&display=swap">
<style>
  :root {
    --navy: #2c3e91;
    --green: #8cc63f;
    --cyan: #23a9de;
    --grey: #6f7073;
    --paper: #fbfbfa;
    --backdrop: #e4e4e2;
  }
  * { margin: 0; padding: 0; box-sizing: border-box; }
  html, body {
    width: 1200px; height: 801px; overflow: hidden;
    background: var(--backdrop);
    font-family: "Josefin Sans", sans-serif;
  }
  .stage {
    position: relative; width: 1200px; height: 801px;
    display: flex; align-items: center; justify-content: center; gap: 40px;
  }
  .card {
    position: relative; width: 540px; height: 309px;
    background: var(--paper);
    box-shadow: 0 6px 18px rgba(0,0,0,0.12);
    overflow: hidden;
  }

  /* Contact side */
  .contact-card .brand {
    position: absolute; left: 48px; top: 42px;
    font-weight: 700; font-size: 40px; color: var(--navy); letter-spacing: -0.5px;
  }
  .person { position: absolute; left: 48px; top: 112px; }
  .person-name { font-weight: 600; font-size: 22px; color: var(--navy); letter-spacing: 0.5px; }
  .person-role { font-weight: 300; font-size: 16px; color: var(--grey); margin-top: 4px; letter-spacing: 0.5px; }
  .dash-row { display: flex; gap: 6px; margin-top: 14px; }
  .dash-row span { display: block; width: 26px; height: 3px; }
  .dash-row .d-navy { background: var(--navy); }
  .dash-row .d-green { background: var(--green); }
  .dash-row .d-cyan { background: var(--cyan); }
  .contact-list {
    position: absolute; left: 48px; bottom: 34px;
    list-style: none; font-weight: 300; font-size: 13px; color: var(--grey);
  }
  .contact-list li { display: flex; align-items: center; gap: 9px; margin-top: 7px; }
  .contact-list .web-text strong { font-weight: 600; color: var(--navy); }
  .icon { width: 15px; height: 15px; flex: none; }

  /* Front side */
  .front-card .brand-block { position: absolute; left: 150px; top: 78px; }
  .front-card .brand {
    display: flex; align-items: center; gap: 12px;
    font-weight: 700; font-size: 54px; color: var(--navy); letter-spacing: -0.5px;
  }
  .brand-dot { width: 18px; height: 18px; border-radius: 50%; background: var(--green); }
  .tagline { font-weight: 400; font-size: 16px; color: var(--grey); margin-top: 4px; letter-spacing: 0.4px; }
  .colour-band {
    position: absolute; left: 0; bottom: 22px; width: 540px; height: 34px;
    background: linear-gradient(90deg, var(--cyan) 0%, var(--green) 50%, var(--navy) 100%);
  }
</style>
</head>
<body>
<main class="stage">

  <section class="card contact-card">
    <div class="brand">BrivoTerna</div>
    <div class="person">
      <div class="person-name">Teodoro Vinsquel</div>
      <div class="person-role">CEO &amp; Founder</div>
      <div class="dash-row"><span class="d-navy"></span><span class="d-green"></span><span class="d-cyan"></span></div>
    </div>
    <ul class="contact-list">
      <li>
        <svg class="icon" viewBox="0 0 16 16" aria-hidden="true"><circle cx="8" cy="8" r="8" fill="var(--green)"/><rect x="4" y="5" width="8" height="6" fill="none" stroke="#fff" stroke-width="1"/><path d="M4 5 L8 8.5 L12 5" fill="none" stroke="#fff" stroke-width="1"/></svg>
        <span>teodoro.vinsquel@brivoterna-example.com</span>
      </li>
      <li><span class="icon"></span><span class="web-text">www.<strong>brivoterna-example</strong>.com</span></li>
      <li>
        <svg class="icon" viewBox="0 0 16 16" aria-hidden="true"><circle cx="8" cy="8" r="8" fill="var(--cyan)"/><path d="M5.5 4.5 L7 4.5 L7.6 6.3 L6.7 7 Q7.5 8.7 9 9.3 L9.7 8.4 L11.5 9 L11.5 10.5 Q7.5 11 5.5 4.5 Z" fill="#fff"/></svg>
        <span>+34 655.803.912</span>
      </li>
    </ul>
  </section>

  <section class="card front-card">
    <div class="brand-block">
      <div class="brand"><span class="brand-dot"></span>BrivoTerna</div>
      <div class="tagline">Lantern of the Steady Harvest</div>
    </div>
    <div class="colour-band" role="img" aria-label="Decorative band in cyan, green and blue for strategy, execution and results"></div>
  </section>

</main>
</body>
</html>
```